Business Card Design for company

We want new business cards. We'd like something different-- yet still highly professional. Our tagline is Providing leadership, delivering success. Stock photos are ok, as long as they are relevant and look upscale.

Target Market(s)

Architecture/Business Management Consulting/Engineering Consulting

Contact Information for Business Card

dark gray background with pops of blue might be good, but you tell me. You're the designers. Rounded corners might be nice, but again, you tell me.

Font styles to use
Serif
Sans Serif

Colors
3276b5
5c5c5c
9d9d9d
fbfbfb

Requirements
Nice to have
• Something different, but still very professional.

```html
<!DOCTYPE html>
<html lang="en">
<head>
<meta charset="utf-8">
<title>Vantrel Advisory – Business Card</title>
<link rel="stylesheet" href="https://fonts.googleapis.com/css2?family=Roboto:wght@400;500;700&display=swap">
<style>
  :root {
    --backdrop: #2b2b2b;
    --card-white: #ffffff;
    --card-slate: #4b4e53;
    --brand-blue: #2c6aa5;
    --text-grey: #5c5c5c;
    --divider: #9d9d9d;
    --tagline: #fbfbfb;
  }
  * { margin: 0; padding: 0; box-sizing: border-box; }
  html, body {
    width: 1125px;
    height: 1200px;
    overflow: hidden;
    background: var(--backdrop);
    font-family: "Roboto", Arial, sans-serif;
  }
  .card {
    position: absolute;
    left: 150px;
    width: 826px;
    height: 471px;
  }
  .card--front { top: 98px; background: var(--card-white); }
  .card--back  { top: 631px; background: var(--card-slate); }

  .front-wordmark {
    position: absolute;
    left: 60px;
    top: 0;
    width: 340px;
    height: 471px;
    display: flex;
    align-items: center;
    justify-content: center;
    font-weight: 700;
    font-size: 62px;
    letter-spacing: 2px;
    color: var(--brand-blue);
  }
  .divider {
    position: absolute;
    left: 427px;
    top: 88px;
    width: 2px;
    height: 292px;
    background: linear-gradient(to bottom, rgba(157,157,157,0), var(--divider) 20%, var(--divider) 80%, rgba(157,157,157,0));
  }
  .contact {
    position: absolute;
    left: 465px;
    top: 100px;
    color: var(--text-grey);
  }
  .contact__name {
    font-weight: 700;
    font-size: 29px;
    color: var(--brand-blue);
    line-height: 1.1;
  }
  .contact__title {
    font-weight: 500;
    font-size: 20px;
    line-height: 1.3;
    margin-bottom: 16px;
  }
  .contact__address {
    font-size: 19px;
    line-height: 25px;
    margin-bottom: 12px;
  }
  .contact__list { list-style: none; }
  .contact__item {
    display: flex;
    align-items: center;
    font-size: 19px;
    line-height: 26px;
  }
  .contact__icon {
    width: 20px;
    height: 20px;
    margin-right: 12px;
    fill: var(--brand-blue);
    flex: none;
  }
  .back-wordmark {
    position: absolute;
    left: 0;
    right: 0;
    top: 165px;
    text-align: center;
    font-weight: 500;
    font-size: 110px;
    letter-spacing: 4px;
    color: var(--tagline);
  }
  .tagline {
    position: absolute;
    left: 0;
    right: 0;
    top: 395px;
    text-align: center;
    font-size: 20px;
    color: var(--tagline);
  }
  .tagline__dot { margin: 0 10px; }
</style>
</head>
<body>
  <section class="card card--front">
    <div class="front-wordmark">VANTREL</div>
    <div class="divider"></div>
    <div class="contact">
      <p class="contact__name">DANIEL MORROW</p>
      <p class="contact__title">CEO/FOUNDER</p>
      <p class="contact__address">2190 Birchwood Court<br>Fairbanks, Alaska 99712</p>
      <ul class="contact__list">
        <li class="contact__item">
          <svg class="contact__icon" viewBox="0 0 24 24"><path d="M6.6 10.8c1.4 2.8 3.8 5.1 6.6 6.6l2.2-2.2c.3-.3.7-.4 1-.2 1.1.4 2.3.6 3.6.6.6 0 1 .4 1 1V20c0 .6-.4 1-1 1C10.6 21 3 13.4 3 4c0-.6.4-1 1-1h3.5c.6 0 1 .4 1 1 0 1.3.2 2.5.6 3.6.1.3 0 .7-.2 1l-2.3 2.2z"/></svg>
          907 555 0142
        </li>
        <li class="contact__item">
          <svg class="contact__icon" viewBox="0 0 24 24"><path d="M16 1H8C6.9 1 6 1.9 6 3v18c0 1.1.9 2 2 2h8c1.1 0 2-.9 2-2V3c0-1.1-.9-2-2-2zm0 17H8V4h8v14z"/></svg>
          907 555 0187
        </li>
        <li class="contact__item">
          <svg class="contact__icon" viewBox="0 0 24 24"><path d="M7 3h10v5H7zM4 9h16c1.1 0 2 .9 2 2v7h-4v3H6v-3H2v-7c0-1.1.9-2 2-2zm4 7v3h8v-3H8z"/></svg>
          907 555 0163
        </li>
        <li class="contact__item">
          <svg class="contact__icon" viewBox="0 0 24 24"><path d="M3 6h18v12H3zM3 6l9 7 9-7" fill="none" stroke="#2c6aa5" stroke-width="2"/></svg>
          daniel@vantreladvisory.com
        </li>
        <li class="contact__item">
          <svg class="contact__icon" viewBox="0 0 24 24"><circle cx="12" cy="12" r="9" fill="none" stroke="#2c6aa5" stroke-width="2"/><path d="M3 12h18M12 3c3 3 3 15 0 18M12 3c-3 3-3 15 0 18" fill="none" stroke="#2c6aa5" stroke-width="1.6"/></svg>
          www.vantreladvisory.com
        </li>
      </ul>
    </div>
  </section>

  <section class="card card--back">
    <div class="back-wordmark">VANTREL</div>
    <p class="tagline">Providing leadership<span class="tagline__dot">•</span>delivering success</p>
  </section>
</body>
</html>
```